Rosko Tamblin

I am a songwriter and would like to include a bio, pictures, discography, CD covers and access to some of my music

Target Market(s)

Music Lovers, songwriters publishers

Coding

Coded - Design and coding required

Number of Pages Required

5+ page

Requirements
Must have
• Pictures of my CD covers, pictures of me and either my Music or links to my music
Nice to have
Should not have
• cartoons

```html
<!DOCTYPE html>
<html lang="en">
<head>
<meta charset="utf-8">
<title>Rosko Tamblin — Songwriter</title>
<link rel="stylesheet" href="https://fonts.googleapis.com/css2?family=Playfair+Display:ital,wght@0,400;0,700;1,400&family=Oswald:wght@300;500&family=Montserrat:wght@400&display=swap">
<style>
:root{
  --ink:#1d1d1f;
  --blue:#3a5fad;
  --maroon:#3a0e06;
  --white:#ffffff;
  --ghost:#eef0f6;
}
*{margin:0;padding:0;box-sizing:border-box}
html,body{width:1200px;height:3750px;overflow:hidden;background:var(--white)}
body{position:relative;font-family:"Playfair Display",serif;color:var(--ink)}
.abs{position:absolute}

/* hero */
.hero{left:0;top:0;width:1200px;height:751px;
  background:radial-gradient(ellipse at 30% 85%,#e8741c 0%,#a9380b 22%,transparent 50%),
             radial-gradient(ellipse at 75% 40%,#6b4a38 0%,transparent 35%),
             linear-gradient(180deg,#120805 0%,#2a0e06 45%,#7a2a08 80%,#c9580f 100%)}
.brand{display:flex;align-items:center;gap:12px;font-family:"Oswald",sans-serif;font-weight:300;font-size:30px;color:var(--white);letter-spacing:.5px;white-space:nowrap}
.brand .dot{width:14px;height:14px;background:var(--white)}
.hero-brand{left:172px;top:40px}
.nav{left:597px;top:63px;display:flex;gap:20px;font-family:"Oswald",sans-serif;font-weight:500;font-size:18px;color:var(--white);text-transform:uppercase;white-space:nowrap}
.hero-title{left:172px;top:215px;font-size:88px;color:var(--white);line-height:1.25}
.hero-title .band{display:inline-block;background:rgba(40,30,28,.82);padding:0 30px 4px 16px;margin-left:-16px}

/* bio */
.bio-card{left:172px;top:552px;width:855px;height:384px;background:var(--white);box-shadow:0 6px 24px rgba(0,0,0,.18)}
.eyebrow{font-style:italic;font-size:20px;color:var(--ink)}
.bio-card .eyebrow{position:absolute;left:27px;top:28px}
.bio-name{position:absolute;left:27px;top:58px;font-weight:700;font-size:37px;line-height:1.25;color:var(--blue)}
.bio-photo{position:absolute;left:27px;top:169px;width:220px;height:176px;background:linear-gradient(160deg,#5f7d45,#a7b68c 50%,#e4e1da)}
.bio-text{position:absolute;left:278px;top:34px;width:555px;font-style:italic;font-size:13px;line-height:29.5px;color:#333}
.bio-text p+p{margin-top:12px}

/* section headings */
.section-head{left:0;width:1200px;text-align:center}
.section-head .ghost{position:absolute;left:0;width:100%;text-align:center;font-weight:700;font-size:100px;color:var(--ghost);letter-spacing:1px;white-space:nowrap}
.section-head .eyebrow{position:relative}
.section-head h2{position:relative;font-weight:700;font-size:37px;color:var(--blue)}

/* covers */
.covers-band{left:0;top:1749px;width:1200px;height:454px;background:var(--maroon)}
.covers-head .ghost{color:rgba(255,255,255,.07)}
.covers-head .eyebrow,.covers-head h2{color:var(--white)}
.cd{border:4px solid var(--white);box-shadow:0 6px 22px rgba(0,0,0,.3)}
.dots{left:568px;top:2455px;display:flex;gap:8px}
.dots span{width:16px;height:16px;border-radius:50%;background:#c5cde6}
.dots span:first-child{background:var(--blue)}

/* gallery */
.tile{position:absolute}

/* albums */
.albums{left:0;top:3244px;width:1200px;height:384px;background:var(--blue)}
.albums .eyebrow{position:absolute;left:172px;top:160px;color:var(--white)}
.albums h2{position:absolute;left:172px;top:190px;font-weight:700;font-size:36px;color:var(--white)}
.album{position:absolute;top:68px;width:216px}
.album .art{position:relative;height:197px;border:2px solid var(--white)}
.album .art svg{position:absolute;left:82px;top:72px}
.album h3{margin-top:18px;font-weight:700;font-size:17px;color:var(--white);white-space:nowrap}
.album p{font-weight:700;font-size:15px;color:var(--white)}

/* footer */
.footer-brand{left:172px;top:3674px;color:var(--blue);font-size:28px}
.footer-brand .dot{background:var(--blue)}
.copyright{right:173px;top:3686px;font-family:"Montserrat",sans-serif;font-size:13px;color:var(--ink)}
.edition{left:1100px;top:3686px;font-family:"Montserrat",sans-serif;font-size:13px;color:var(--ink)}
</style>
</head>
<body>

<header class="hero abs" role="img" aria-label="Rosko Tamblin standing at night in front of a glowing fire crater"></header>
<div class="brand hero-brand abs"><span class="dot"></span>Rosko Tamblin</div>
<nav class="nav abs"><span>Home</span><span>Bio</span><span>Pictures</span><span>Discography</span><span>CD Covers</span><span>Contact</span></nav>
<h1 class="hero-title abs">Rosko<br><span class="band">Tamblin</span></h1>

<section class="bio-card abs">
  <div class="eyebrow">BIO</div>
  <div class="bio-name">ROSKO<br>TAMBLIN</div>
  <div class="bio-photo" role="img" aria-label="Portrait of Rosko Tamblin in a straw hat outdoors"></div>
  <div class="bio-text">
    <p>Rosko Tamblin was born and raised in Port Alder, Texas. He began playing music at the age of eight when his sister returned home from summer camp and asked her parents to buy her a baritone ukulele. She taught her younger brother some chords on the ukulele and he was hooked. The following spring, they went to one of the border towns in Mexico and bought a Mexican guitar for $12. They restrung it with nylon strings and Tamblin began to learn how to play the guitar. He took guitar lessons at a local music store and learned how to play the hits of the day by groups like the Velvet Lanterns, the Drifting Foxes, and the Kestrels.</p>
    <p>He got his first electric guitar when he was about 10 years old. He began jamming with other musicians when he was 13 or 14. They were much more experienced than he and introduced him to the blues.</p>
  </div>
</section>

<div class="section-head abs" style="top:1005px">
  <div class="ghost" style="top:0">DISCOGRAPHY</div>
  <div class="eyebrow" style="top:22px">MY</div>
  <h2 style="top:20px">DISCOGRAPHY</h2>
</div>

<svg class="abs" style="left:0;top:1150px" width="1200" height="540" aria-hidden="true">
  <defs>
    <radialGradient id="floor" cx="50%" cy="50%" r="50%"><stop offset="0" stop-color="#000" stop-opacity=".28"/><stop offset="1" stop-color="#000" stop-opacity="0"/></radialGradient>
  </defs>
  <ellipse cx="380" cy="248" rx="240" ry="22" fill="url(#floor)"/>
  <ellipse cx="850" cy="248" rx="240" ry="22" fill="url(#floor)"/>
  <ellipse cx="580" cy="510" rx="250" ry="22" fill="url(#floor)"/>
  <g>
    <circle cx="438" cy="135" r="108" fill="#111"/>
    <circle cx="438" cy="135" r="92" fill="none" stroke="#2b2b2b"/>
    <circle cx="438" cy="135" r="76" fill="none" stroke="#2b2b2b"/>
    <circle cx="438" cy="135" r="32" fill="#e6e6e6"/>
  </g>
  <g>
    <circle cx="907" cy="135" r="108" fill="#111"/>
    <circle cx="907" cy="135" r="92" fill="none" stroke="#2b2b2b"/>
    <circle cx="907" cy="135" r="76" fill="none" stroke="#2b2b2b"/>
    <circle cx="907" cy="135" r="32" fill="#e6e6e6"/>
  </g>
  <g>
    <rect x="352" y="288" width="442" height="217" rx="108" fill="#111"/>
    <circle cx="460" cy="396" r="32" fill="#e6e6e6"/>
    <circle cx="686" cy="396" r="32" fill="#e6e6e6"/>
  </g>
</svg>
<div class="abs" style="left:211px;top:1176px;width:226px;height:217px;background:linear-gradient(135deg,#1ec07a,#e8e04a 45%,#d8272a 80%)" role="img" aria-label="Album cover: Rosko Tamblin playing guitar in vivid colour"></div>
<div class="abs" style="left:680px;top:1176px;width:227px;height:217px;background:linear-gradient(135deg,#d9d9d9,#333 50%,#111)" role="img" aria-label="Album cover: black and white high-contrast guitarist in a hat"></div>
<div class="abs" style="left:460px;top:1438px;width:224px;height:217px;background:linear-gradient(180deg,#0d0d0d,#2f6b1e 35%,#8bc34a 60%,#143d0e 85%,#0d0d0d)" role="img" aria-label="Album cover: Lanterns in the Pines, sunlit green forest"></div>

<div class="covers-band abs"></div>
<div class="section-head covers-head abs" style="top:1818px">
  <div class="ghost" style="top:0">CD COVERS</div>
  <div class="eyebrow" style="top:22px">MY</div>
  <h2 style="top:20px">CD COVERS</h2>
</div>
<div class="cd abs" style="left:172px;top:1996px;width:190px;height:380px;background:linear-gradient(160deg,#f2d34a,#e5531a 40%,#2a2a52 80%,#0e0e20)" role="img" aria-label="CD cover with flames and a burning book"></div>
<div class="cd abs" style="left:838px;top:1996px;width:189px;height:380px;background:linear-gradient(170deg,#3a3f6e,#6b6f9a 35%,#1c1c2a 70%,#d95f1a 100%)" role="img" aria-label="CD cover with a silhouetted man under lightning"></div>
<div class="cd abs" style="left:357px;top:1970px;width:486px;height:432px;background:radial-gradient(ellipse at 50% 45%,#ff8a1e 0%,#c23d0b 25%,#0a0a0a 55%)" role="img" aria-label="CD cover: Lanterns in the Pines, Rosko Tamblin before a fire crater, with track list"></div>
<div class="dots abs"><span></span><span></span><span></span></div>

<div class="section-head abs" style="top:2572px">
  <div class="ghost" style="top:0">GALLERY</div>
  <div class="eyebrow" style="top:22px">MY</div>
  <h2 style="top:20px">GALLERY</h2>
</div>
<div class="tile" style="left:172px;top:2705px;width:338px;height:446px;background:linear-gradient(160deg,#a88b62,#c9ad85 40%,#e9e6df 70%,#8a6f4c)" role="img" aria-label="Rosko Tamblin in a white shirt holding a hat by an adobe wall"></div>
<div class="tile" style="left:524px;top:2705px;width:503px;height:248px;background:linear-gradient(135deg,#111,#5a5a5a 45%,#0c0c0c)" role="img" aria-label="Black and white guitarist in a hat"></div>
<div class="tile" style="left:524px;top:2970px;width:243px;height:181px;background:linear-gradient(160deg,#5f7d45,#a7b68c 50%,#e4e1da)" role="img" aria-label="Rosko Tamblin in a straw hat outdoors"></div>
<div class="tile" style="left:783px;top:2970px;width:244px;height:181px;background:radial-gradient(ellipse at 40% 70%,#ff7a18,#a8300a 45%,#120604 85%)" role="img" aria-label="Rosko Tamblin at night before a fire crater"></div>

<section class="albums abs">
  <div class="eyebrow">MY</div>
  <h2>ALBUMS</h2>
  <div class="album" style="left:361px">
    <div class="art" style="background:linear-gradient(180deg,#0d0d0d,#2f6b1e 40%,#7fb548 65%,#143d0e 90%)" role="img" aria-label="Lanterns in the Pines album art, green forest">
      <svg width="52" height="52" viewBox="0 0 52 52"><circle cx="26" cy="26" r="23" fill="none" stroke="#fff" stroke-width="3"/><path d="M21 16 L36 26 L21 36 Z" fill="#fff"/></svg>
    </div>
    <h3>Lanterns in the Pines</h3><p>2019</p>
  </div>
  <div class="album" style="left:585px">
    <div class="art" style="background:linear-gradient(135deg,#e53a2a,#f2c230 30%,#2b4fb8 60%,#1b1b1b 85%)" role="img" aria-label="Open Palms album art, colourful abstract painting">
      <svg width="52" height="52" viewBox="0 0 52 52"><circle cx="26" cy="26" r="23" fill="none" stroke="#fff" stroke-width="3"/><path d="M21 16 L36 26 L21 36 Z" fill="#fff"/></svg>
    </div>
    <h3>Open Palms</h3><p>2017</p>
  </div>
  <div class="album" style="left:811px">
    <div class="art" style="background:linear-gradient(170deg,#566a7a,#93a3ab 40%,#3d5260 75%,#b26b2a)" role="img" aria-label="Salt and Thunder album art with stormy sea waves">
      <svg width="52" height="52" viewBox="0 0 52 52"><circle cx="26" cy="26" r="23" fill="none" stroke="#fff" stroke-width="3"/><path d="M21 16 L36 26 L21 36 Z" fill="#fff"/></svg>
    </div>
    <h3>Open Palms</h3><p>2017</p>
  </div>
</section>

<footer>
  <div class="brand footer-brand abs"><span class="dot"></span>Rosko Tamblin</div>
  <p class="copyright abs">Copyrights @ 2020 Rosko Tamblin. All Rights Reserved.</p>
  <p class="edition abs">C20</p>
</footer>

</body>
</html>
```